Heron Haulage needs Bussiness cards!

Our new trucking company needs business cards!
We need the same design with two different names and emails, everything else it's the same.
I have included our original logo so we can use it for the design.
Note: the logo to be used is the o e with the buffalo on the right side, next to the letters H and H.

Target Market(s)

Trucking, refrigerated transportation, freight

Industry/Entity Type

Business

Contact Information for Business Card

Card #1:
Marcus Whitfield
marcuswhitfield@heronhaulage.example
1-855-317-6094
(555)238-7160
4117 W. Larkin Ave.
Alderby, NV 78590
www.heronhaulage.example

Card#2:
Rosalba Quintero
rosalba@heronhaulage.example
1-855-317-6094
(555)238-7160
4117 W. Larkin Ave.
Alderby, NV 78590
www.heronhaulage.example

Font styles to use
Sans Serif

Colors
0655a3
ec1f27
ffffff

Requirements
Must have
• our logo
Nice to have
• roads on background,

```html
<!DOCTYPE html>
<html lang="en">
<head>
<meta charset="utf-8">
<title>Heron Haulage – Business Cards</title>
<link href="https://fonts.googleapis.com/css2?family=Source+Sans+3:wght@400;800&display=swap" rel="stylesheet">
<style>
  :root {
    --brand-blue: #0655a3;
    --brand-red: #ec1f27;
    --paper: #ffffff;
    --backdrop: #3b3b3b;
    --ink: #3a3a3a;
  }
  * { margin: 0; padding: 0; box-sizing: border-box; }
  html, body {
    width: 1200px; height: 1200px; overflow: hidden;
    background: var(--backdrop);
    font-family: "Source Sans 3", sans-serif;
  }
  .card {
    position: absolute;
    left: 294px;
    width: 612px;
    height: 347px;
    background: var(--paper);
    overflow: hidden;
  }
  .card--front { top: 218px; }
  .card--back { top: 637px; }

  .wordmark {
    position: absolute;
    display: flex;
    align-items: center;
    gap: 12px;
    color: var(--brand-blue);
    font-weight: 800;
    white-space: nowrap;
    line-height: 1;
  }
  .wordmark__dot {
    width: 0.55em; height: 0.55em;
    border-radius: 50%;
    background: var(--brand-red);
    flex: none;
  }
  .card--front .wordmark { left: 0; right: 0; top: 145px; justify-content: center; font-size: 54px; }
  .card--back .wordmark { left: 28px; top: 62px; font-size: 50px; }

  .front-stripe { position: absolute; left: 0; right: 0; bottom: 0; height: 12px; display: flex; }
  .front-stripe__red { flex: 1; background: var(--brand-red); }
  .front-stripe__blue { flex: 1; background: var(--brand-blue); }

  .name-marker { position: absolute; left: 0; top: 199px; width: 12px; height: 35px; background: var(--brand-red); }
  .holder-name {
    position: absolute; left: 28px; top: 200px;
    font-size: 28px; font-weight: 400; color: var(--brand-blue);
  }
  .contact-list { position: absolute; left: 28px; top: 254px; list-style: none; }
  .contact-list li {
    display: flex; align-items: center; gap: 8px;
    height: 20px; font-size: 16px; color: var(--ink);
  }
  .contact-list svg { width: 14px; height: 14px; fill: var(--brand-red); flex: none; }
  .address {
    position: absolute; right: 26px; top: 254px;
    text-align: right; font-size: 16px; line-height: 20px; color: var(--ink); font-style: normal;
  }
  .swoosh { position: absolute; left: 0; bottom: 0; width: 612px; height: 46px; }
  .web {
    position: absolute; right: 24px; bottom: 9px;
    font-size: 16px; color: var(--paper);
  }
</style>
</head>
<body>
  <section class="card card--front">
    <div class="wordmark"><span class="wordmark__dot"></span>Heron Haulage</div>
    <div class="front-stripe"><span class="front-stripe__red"></span><span class="front-stripe__blue"></span></div>
  </section>

  <section class="card card--back">
    <div class="wordmark"><span class="wordmark__dot"></span>Heron Haulage</div>
    <span class="name-marker"></span>
    <h1 class="holder-name">Marcus Whitfield</h1>
    <ul class="contact-list">
      <li><svg viewBox="0 0 14 14"><path d="M1 3h12v8H1z M1 3l6 5 6-5" fill="var(--brand-red)"/><path d="M1.5 3.5l5.5 4.5 5.5-4.5" stroke="#fff" stroke-width="1.2" fill="none"/></svg>marcuswhitfield@heronhaulage.example</li>
      <li><svg viewBox="0 0 14 14"><path d="M1 5c0-2 3-3 6-3s6 1 6 3v1h-3V4.5C9 4 5 4 4 4.5V6H1z M3 7h8l1 5H2z"/><circle cx="7" cy="9.3" r="1.4" fill="#fff"/></svg>1-855-317-6094</li>
      <li><svg viewBox="0 0 14 14"><path d="M4 1h6a1 1 0 0 1 1 1v10a1 1 0 0 1-1 1H4a1 1 0 0 1-1-1V2a1 1 0 0 1 1-1z M4.5 2.5v8h5v-8z"/></svg>(555)238-7160</li>
    </ul>
    <address class="address">4117 W. Larkin Ave.<br>Alderby, NV 78590</address>
    <svg class="swoosh" viewBox="0 0 612 46" aria-hidden="true">
      <path d="M306 46 C340 28 380 16 420 10 L430 10 C390 18 352 30 324 46 Z" fill="var(--brand-blue)"/>
      <path d="M338 46 C365 28 390 12 410 5 Q420 1 440 0 L612 0 L612 46 Z" fill="var(--brand-red)"/>
    </svg>
    <span class="web">www.heronhaulage.example</span>
  </section>
</body>
</html>
```